Maple Bus Card

i own a building in the bronx ny - its called "Maple 7 on 2 HDFC"i want a classy logo / business card - nothing too religuous but it is like a family there - its a large apartment building - colors i like dark red, black, medium shade of gray also reg business card stuff tel # 914-555-0173 address 4738 Larkwell Ave Bronx NY 10460 Email fijosh@aol.comslogan - " from many we are one "i can send u a picture of the building for the backside

```html
<!DOCTYPE html>
<html lang="en">
<head>
<meta charset="utf-8">
<title>Maple 7 on 2 HDFC – Business Card</title>
<link rel="stylesheet" href="https://fonts.googleapis.com/css2?family=Roboto:wght@500;700&family=Open+Sans:wght@400;600&display=swap">
<style>
  :root {
    --backdrop: #989898;
    --card-dark: #2b2b2b;
    --accent-gold: #f2b516;
    --text-gray: #c4c4c4;
    --text-light: #e6e6e6;
    --rule-gray: #7a7a7a;
    --brick-light: #8a4434;
    --brick-dark: #4e2520;
  }
  * { margin: 0; padding: 0; box-sizing: border-box; }
  html, body { width: 1200px; height: 900px; overflow: hidden; background: var(--backdrop); }
  .canvas { position: relative; width: 1200px; height: 900px; }

  .card {
    position: absolute; top: 200px; width: 310px; height: 503px;
    box-shadow: 2px 3px 6px rgba(0,0,0,0.35);
  }
  .card-front {
    left: 253px; background: var(--card-dark);
    border-radius: 46px 4px 46px 4px;
    font-family: "Open Sans", sans-serif; color: var(--text-light);
  }
  .card-back {
    left: 627px;
    border-radius: 4px 46px 4px 46px;
    background: linear-gradient(180deg, var(--brick-light) 0%, #743729 55%, var(--brick-dark) 88%, #3a3a40 100%);
  }

  .brand-mark {
    position: absolute; left: 50%; top: 82px; width: 64px; height: 64px;
    margin-left: -32px; border-radius: 50%; background: #8f8f8f;
  }
  .brand-name {
    position: absolute; left: 0; right: 0; top: 162px; text-align: center;
    font-family: "Roboto", sans-serif; font-weight: 700; color: var(--accent-gold);
    font-size: 36px; line-height: 44px; letter-spacing: 0.5px;
  }
  .brand-sub {
    position: absolute; left: 30px; right: 30px; top: 205px;
    display: flex; align-items: center; gap: 8px;
    font-family: "Roboto", sans-serif; font-weight: 700; color: var(--accent-gold);
    font-size: 15px; letter-spacing: 1px;
  }
  .brand-sub::before, .brand-sub::after {
    content: ""; flex: 1; height: 1px; background: var(--rule-gray);
  }
  .slogan {
    position: absolute; left: 0; right: 0; top: 240px; text-align: center;
    font-family: "Roboto", sans-serif; font-weight: 500; color: var(--text-gray);
    font-size: 16px; letter-spacing: 1px;
  }

  .contact { position: absolute; left: 32px; top: 315px; }
  .person-name {
    font-family: "Roboto", sans-serif; font-weight: 700; color: var(--accent-gold);
    font-size: 19px; line-height: 24px;
  }
  .person-role { font-size: 14px; color: var(--text-gray); line-height: 20px; }
  .details { margin-top: 16px; list-style: none; font-size: 14px; line-height: 19px; }
  .details li { display: flex; align-items: center; gap: 6px; }
  .details svg { width: 14px; height: 12px; fill: var(--accent-gold); }
  .address { margin-top: 13px; font-size: 14px; line-height: 19px; font-style: normal; }
</style>
</head>
<body>
<main class="canvas">
  <section class="card card-front">
    <div class="brand-mark"></div>
    <h1 class="brand-name">MAPLE 7 ON 2</h1>
    <div class="brand-sub">HDFC</div>
    <p class="slogan">FROM MANY WE ARE ONE</p>

    <div class="contact">
      <p class="person-name">DANIEL OKORO</p>
      <p class="person-role">Managing Director</p>
      <ul class="details">
        <li>
          <svg viewBox="0 0 14 12" aria-hidden="true"><path d="M1 4 Q7 -1 13 4 L11 5.5 L9.5 3.5 L4.5 3.5 L3 5.5 Z M3.5 6 L10.5 6 L12 11 L2 11 Z"/></svg>
          914-555-0173
        </li>
        <li>
          <svg viewBox="0 0 14 12" aria-hidden="true"><path d="M1 2 H13 V11 H1 Z" /><path d="M1 2 L7 7 L13 2" fill="none" stroke="#2b2b2b" stroke-width="1.3"/></svg>
          mavreld@quintmail.com
        </li>
      </ul>
      <address class="address">4738 Larkwell Ave<br>Bronx NY 10460</address>
    </div>
  </section>

  <section class="card card-back" role="img" aria-label="Photograph of the red-brick apartment building with fire escapes, its entrance and cars parked on the street in front"></section>
</main>
</body>
</html>
```